Plinkbase Design Project

We are looking for a new design for our website - and need your help to make it great.

Our current website is here: http://www.korvel.com: It has way too much information on it and it lacks a clear focus.

You can download the current design approach here: http://fx.qz/pRdw83knab

It is a layered PSD file with the various approved images for the different sections. We have also uploaded images to the project which you can use.

Please use these section images in your designs with improvement suggestions as per below.

What we still need:

Header: We are not entirely sure about the header yet - variations for this would be great.

Colour scheme: We are not sure about the colour scheme yet: if you have better ideas, please present them. May be less colours, or muted colours ?

Improvements required to section images:

Full design Freedom: The monitor with t-shirts is fine, the middle screen should be a gallery of modern watches (image provided or you can create a better one) and the fruits - image provided (see attached image Korvel_site_development_blue-header)

Many product types: really only the text in the bubbles needs some improvements

Main Website Font:

The font in the supplied PSD file is a Brimlet web font called Open Sans http://www.brimlet.com/fonts/specimen/Open+Sans

This font is quite nice, but not so easy to read on some backgrounds. It can be replaced with a stronger font which does not look too heavy or playful.

Font for: "Click on any T-Shirt to see how it works": http://www.quonfield.com.au/type/sketch.html. If you can think of a nicer handwritten code you are welcome - I am happy with this one.

we are also lacking the additional page designs - content, blog, contact, pricing and so on.

We are quite far down the track with this design - only participate if you think you can create a genuinely better and stronger approach.
Updates

Target Market(s)

Designers and small business owners

Industry/Entity Type

Brimlet

Requirements
Must have
• Home page (improvement of current approach)
Note that text and section images are approved apart from those listed above - so only create others if you can do genuinely better
content page
contact page
A better footer
blog design
pricing page
Nice to have
• anything else you can come up with to make the site look more appealing and professional.

We only need designs - and layered psd files - programming will be a separate task
Should not have
• Photos which are TOO stock style. We use pixmarrow and vantuzo

```html
<!DOCTYPE html>
<html lang="en">
<head>
<meta charset="utf-8">
<title>Korvel – The last ecommerce solution</title>
<link href="https://fonts.googleapis.com/css2?family=PT+Sans:wght@400;700&family=Roboto+Condensed:wght@300;400&family=Ubuntu:wght@700&display=swap" rel="stylesheet">
<style>
:root{
  --brand-blue:#0a6ab3;
  --link-blue:#1270b5;
  --accent-orange:#f26a1b;
  --cta-green:#8cb818;
  --cta-green-dark:#6f9512;
  --text-dark:#333;
  --text-mid:#555;
  --text-grey:#9a9a9a;
  --sale-red:#d0121b;
  --white:#fff;
  --line:#d8d8d8;
}
*{margin:0;padding:0;box-sizing:border-box}
html,body{width:1195px;height:1200px;overflow:hidden;background:var(--white)}
body{position:relative;font-family:"PT Sans",sans-serif;color:var(--text-dark)}
.abs{position:absolute}
.top-rule,.bottom-rule{left:0;width:1195px;height:6px;background:var(--brand-blue)}
.top-rule{top:0}.bottom-rule{bottom:0;height:4px}

.brand{left:138px;top:30px;font-family:"Ubuntu",sans-serif;font-weight:700;font-size:38px;color:var(--brand-blue);letter-spacing:-.5px;display:flex;align-items:center;gap:8px}
.brand-dot{width:12px;height:12px;border-radius:50%;background:var(--accent-orange)}

.main-nav{top:41px;left:543px;display:flex;align-items:center;font-family:"Roboto Condensed",sans-serif;font-size:15px}
.main-nav a{color:var(--link-blue);text-decoration:none;margin-right:38px}
.btn{display:inline-flex;align-items:center;justify-content:center;background:linear-gradient(var(--cta-green),var(--cta-green-dark));color:var(--white);text-decoration:none;border-radius:3px;font-family:"Roboto Condensed",sans-serif}
.main-nav .btn{width:111px;height:31px;margin:0;color:var(--white)}

.hero{left:0;top:100px;width:1195px;height:503px;background:var(--brand-blue);overflow:hidden}
.hero-title{left:142px;top:110px;font-family:"Roboto Condensed",sans-serif;font-weight:300;font-size:28px;line-height:41px;color:var(--white)}
.hero-copy{left:142px;top:200px;width:440px;font-size:18px;line-height:30px;color:var(--white)}
.hero-cta{left:142px;top:354px;width:242px;height:51px;font-size:22px}
.hero-cta strong{font-size:30px;font-weight:400;margin:0 6px}
.slider-dots{left:143px;top:448px;display:flex;gap:15px}
.slider-dots span{width:20px;height:20px;border-radius:50%;background:#e4e4e4}
.slider-dots .is-active{background:var(--cta-green)}
.hero-visual{left:585px;top:0;width:610px;height:503px;background:radial-gradient(circle at 45% 55%,#f4f1e6 0,#d9c8a0 30%,#7fa64a 58%,#3f7a2c 80%,#1b5f8d 100%)}

.partners{top:643px;left:130px;width:945px;display:flex;justify-content:space-between;font-family:"Roboto Condensed",sans-serif;font-size:19px;color:var(--text-grey)}

.section-title{font-family:"Roboto Condensed",sans-serif;font-size:22px;color:var(--link-blue)}
.solutions-title{left:128px;top:716px}
.solutions-copy{left:132px;top:754px;width:390px;font-size:14px;line-height:18px;color:var(--text-mid)}
.products{left:132px;top:856px;display:flex;gap:4px}
.product{width:123px;position:relative;height:220px}
.product-photo{width:123px;height:113px;border:1px solid var(--line)}
.product-name{position:absolute;top:124px;left:2px;font-family:"Roboto Condensed",sans-serif;font-size:17px;color:var(--text-dark)}
.product-offer{position:absolute;top:149px;left:5px;font-size:9px;color:var(--sale-red)}
.product-price{position:absolute;top:161px;left:5px;font-size:15px}
.product-price s{margin-right:14px}
.product .btn{position:absolute;top:186px;left:1px;width:91px;height:30px;font-size:15px}
.product:nth-child(2) .btn{left:-3px}

.video-title{left:535px;top:716px}
.video-frame{left:535px;top:755px;width:555px;height:317px;border:3px solid #dcdcdc;background:var(--white)}
.video-screen{position:absolute;left:4px;top:4px;right:4px;bottom:46px;background:linear-gradient(#f7f9fc,#e7edf5)}
.video-controls{position:absolute;left:4px;right:4px;bottom:4px;height:42px;background:linear-gradient(#3a3a3a,#1c1c1c);color:#ddd;font-size:14px;display:flex;align-items:center}
.video-progress{position:absolute;left:4px;right:4px;bottom:46px;height:8px;background:#555}
.video-progress i{display:block;width:45px;height:8px;background:#d40000}
.play-button{position:absolute;left:240px;top:140px}

.footer-shadow{left:105px;top:1103px;width:985px;height:4px;background:linear-gradient(90deg,transparent,#bcbcbc,transparent)}
.footer-nav{left:114px;top:1140px;display:flex;gap:38px;font-family:"Roboto Condensed",sans-serif;font-size:15px}
.footer-nav a{color:#555;text-decoration:none}
.copyright{left:772px;top:1128px;font-family:Arial,sans-serif;font-size:12px;color:#333}
.social{left:950px;top:1162px;display:flex;gap:11px}
.social span{width:31px;height:31px;border-radius:50%;background:#b3b3b3}
.page-code{left:1131px;top:1171px;font-size:13px;color:#555}
</style>
</head>
<body>
<div class="abs top-rule"></div>

<header>
  <div class="abs brand">korvel<span class="brand-dot"></span></div>
  <nav class="abs main-nav">
    <a href="#">HOME</a><a href="#">TOUR</a><a href="#">PRICING</a><a href="#">CONTACT ME</a><a href="#">LOGIN</a>
    <a href="#" class="btn">REGISTER</a>
  </nav>
</header>

<section class="abs hero">
  <h1 class="abs hero-title" style="font-weight:300">THE LAST ECOMMERCE SOLUTION<br>YOU'LL NEED</h1>
  <p class="abs hero-copy">Accept orders from your website, Facemoor, Pinvora, a Plinkbase blog, your Korvel store, eMail, Twindle, Skyvo, SMS, a printed broshures, magazines, radio and TV. Zero programming, total design freedom.</p>
  <a href="#" class="abs btn hero-cta">Its<strong>FREE !</strong>Start Here</a>
  <div class="abs slider-dots"><span class="is-active"></span><span></span><span></span><span></span></div>
  <div class="abs hero-visual" role="img" aria-label="Desktop monitor showing a woman with a grocery bag, surrounded by fresh vegetables"></div>
</section>

<div class="abs partners">
  <span>Paylume</span><span>Veritrove</span><span>Intavo</span><span>Tarnex</span><span>Upsend</span><span>Dalvex</span><span>Fendrix</span><span>Quilbook</span><span>Facemoor</span><span>Plinkbase</span><span>Yonvue</span><span>Pinvora</span>
</div>

<h2 class="abs section-title solutions-title">SIMPLE SOLUTIONS, POWERFUL RESULTS</h2>
<p class="abs solutions-copy">Now you can have kick-ass eCommerce with zero programming. Start selling from anywhere you want in under 60 seconds.<br><br><br>It's almost like magic.</p>

<div class="abs products">
  <article class="product">
    <div class="product-photo" role="img" aria-label="Red bell pepper" style="background:radial-gradient(circle,#d8201a 0,#e84a3a 35%,#fff 62%)"></div>
    <h3 class="product-name" style="font-weight:400">Cool Capsicums</h3>
    <span class="product-offer">SPECIAL OFFER</span>
    <p class="product-price"><s>$ 0.10</s>$0.08</p>
    <a href="#" class="btn">BUY NOW</a>
  </article>
  <article class="product">
    <div class="product-photo" role="img" aria-label="Fresh lemons with leaves" style="background:radial-gradient(circle,#f6dd3a 0,#f0c820 35%,#fff 62%)"></div>
    <h3 class="product-name" style="font-weight:400">Digital lemons</h3>
    <p class="product-price">$ 0.10</p>
    <a href="#" class="btn">BUY NOW</a>
  </article>
  <article class="product">
    <div class="product-photo" role="img" aria-label="Garlic bulbs and cloves" style="background:radial-gradient(circle,#efe6d6 0,#dccbb0 35%,#fff 62%)"></div>
    <h3 class="product-name" style="font-weight:400">Digital garlic</h3>
    <p class="product-price">$ 0.10</p>
    <a href="#" class="btn">BUY NOW</a>
  </article>
</div>

<h2 class="abs section-title video-title">WATCH OUR VIDEO</h2>
<div class="abs video-frame">
  <div class="video-screen" role="img" aria-label="Screen recording of the Korvel store dashboard"></div>
  <svg class="play-button" width="62" height="62" viewBox="0 0 62 62"><circle cx="31" cy="31" r="30" fill="#444" fill-opacity=".85"/><path d="M25 19 L43 31 L25 43 Z" fill="#fff"/></svg>
  <div class="video-progress"><i></i></div>
  <div class="video-controls">
    <svg width="70" height="20" viewBox="0 0 70 20"><path d="M24 2 L40 10 L24 18 Z" fill="#bbb"/><path d="M50 7h4l5-4v14l-5-4h-4z" fill="#bbb"/></svg>
    <span style="margin-left:40px">0:06 <span style="color:#999">/ 1:37</span></span>
  </div>
</div>

<footer>
  <div class="abs footer-shadow"></div>
  <nav class="abs footer-nav"><a href="#">HOME</a><a href="#">TOUR</a><a href="#">PRICING</a><a href="#">CONTACT ME</a><a href="#">LOGIN</a></nav>
  <p class="abs copyright">Copyright &nbsp;©&nbsp; 2013 &nbsp; www.korvel.com &nbsp;All rights reserved.</p>
  <div class="abs social" aria-label="Social links"><span></span><span></span><span></span></div>
  <span class="abs page-code">M1</span>
</footer>

<div class="abs bottom-rule"></div>
</body>
</html>
```